U.S. Popcorn company needs business cards

We are a popcorn company that manufactures popcorn and sells it to grocery stores worldwide. Our theme is "Americana" and our logo is U.S. route 66 which is the most famous highway in the U.S.

We would like the design to be simple and to use both sides. On the back side we would like to see just the logo and website. The front would be normal details

Target Market(s)

Wholesalers, grocers and distributors

Industry/Entity Type

Manufacture

Contact Information for Business Card

Business name: Prairie Lantern Popcorn
Phone: +1 555 308 4726
Email: Dale@prairielanternpopcorn.com
website: www.prairielanternpopcorn.com
Tag Line: "POPular for a reason"
Name: Dale Whitcombe
Title: Founder/President

Requirements
Must have
• Either this design should be fun or clean and simple. I will let you show me your thougths.
Nice to have
• Anything that ties in the real Hwy Route 66.
• Colors might need to be red, white and blue incorporated.
Should not have
• Not be too busy.

```html
<!DOCTYPE html>
<html lang="en">
<head>
<meta charset="utf-8">
<title>Prairie Lantern Popcorn – Business Cards</title>
<link href="https://fonts.googleapis.com/css2?family=Open+Sans:wght@400;600;700&family=Nunito+Sans:wght@400;600;800&display=swap" rel="stylesheet">
<style>
  :root {
    --stage: #3b3b3b;
    --navy: #0b2566;
    --navy-text: #1b2a6b;
    --red: #e31e24;
    --white: #ffffff;
  }
  * { box-sizing: border-box; margin: 0; padding: 0; }
  html, body { width: 1200px; height: 900px; overflow: hidden; }
  body {
    background: var(--stage);
    position: relative;
    font-family: "Open Sans", Arial, sans-serif;
  }
  .card {
    position: absolute;
    width: 347px;
    height: 560px;
    overflow: hidden;
  }
  .card--front { left: 237px; top: 171px; }
  .card--back { left: 649px; top: 169px; background: var(--white); }

  .front__brand-band {
    position: absolute; left: 0; top: 0; width: 100%; height: 335px;
    background: var(--navy);
  }
  .front__contact-band {
    position: absolute; left: 0; top: 335px; width: 100%; height: 225px;
    background: var(--red);
  }

  .brand {
    position: absolute; left: 0; width: 100%;
    display: flex; flex-direction: column; align-items: center;
    font-family: "Nunito Sans", Arial, sans-serif;
    font-weight: 800;
    text-transform: uppercase;
    text-align: center;
  }
  .brand__dot { border-radius: 50%; background: var(--red); }
  .brand--front { top: 78px; color: var(--white); font-size: 30px; line-height: 1.1; gap: 16px; }
  .brand--front .brand__dot { width: 34px; height: 34px; }
  .brand--back { top: 168px; color: var(--navy-text); font-size: 36px; line-height: 1.1; gap: 20px; }
  .brand--back .brand__dot { width: 42px; height: 42px; }

  .tagline {
    position: absolute; left: 0; top: 288px; width: 100%;
    text-align: center; color: var(--white);
    font-family: "Nunito Sans", Arial, sans-serif;
    font-size: 18px; font-weight: 400; letter-spacing: 0.2px;
  }

  .person { position: absolute; left: 31px; top: 56px; color: var(--white); }
  .person__name { font-size: 23px; font-weight: 600; line-height: 1.1; }
  .person__title { font-size: 16px; font-weight: 600; margin-top: 6px; }

  .contact { position: absolute; left: 31px; top: 134px; list-style: none; color: var(--white); }
  .contact__item { display: flex; align-items: center; gap: 7px; font-size: 16px; height: 24px; }
  .contact__icon { width: 13px; height: 13px; flex: none; }

  .website {
    position: absolute; left: 0; top: 486px; width: 100%;
    text-align: center; color: var(--navy-text);
    font-family: "Nunito Sans", Arial, sans-serif;
    font-size: 14px; font-weight: 600; letter-spacing: 0.4px;
  }
</style>
</head>
<body>

  <section class="card card--front" aria-label="Business card front">
    <div class="front__brand-band">
      <div class="brand brand--front">
        <span class="brand__dot"></span>
        <span class="brand__name">Prairie Lantern<br>Popcorn</span>
      </div>
      <p class="tagline">POPULAR FOR A REASON</p>
    </div>
    <div class="front__contact-band">
      <div class="person">
        <p class="person__name">Dale Whitcombe</p>
        <p class="person__title">Founder/President</p>
      </div>
      <ul class="contact">
        <li class="contact__item">
          <svg class="contact__icon" viewBox="0 0 13 13" aria-hidden="true">
            <rect x="3" y="0.5" width="7" height="12" rx="1.2" fill="none" stroke="#fff" stroke-width="1.3"/>
            <rect x="5.5" y="10" width="2" height="1.2" fill="#fff"/>
          </svg>
          +1 555 308 4726
        </li>
        <li class="contact__item">
          <svg class="contact__icon" viewBox="0 0 13 13" aria-hidden="true">
            <rect x="0.5" y="2.5" width="12" height="8" fill="#fff"/>
            <path d="M0.5 2.5 L6.5 7 L12.5 2.5" fill="none" stroke="#e31e24" stroke-width="1"/>
          </svg>
          Dale@prairielanternpopcorn.com
        </li>
      </ul>
    </div>
  </section>

  <section class="card card--back" aria-label="Business card back">
    <div class="brand brand--back">
      <span class="brand__dot"></span>
      <span class="brand__name">Prairie Lantern<br>Popcorn</span>
    </div>
    <p class="website">WWW.PRAIRIELANTERNPOPCORN.COM</p>
  </section>

</body>
</html>
```